Pine Ledge Traders, LLC- Global Beverage Company with 100% Cold Chain Logistics

Hey All, My Name is Dale, I am a young business owner in a competitive export space, but my niche is that I am shipping all of my beer around the world, "100% Cold Chain". This model is more costly, but it protects the integrity of the beer itself and will give folks in foreign countries the best representation of what US Craft Beer has to offer.

I am not a branding guy and don't claim to be one, I am a salesperson first, and will be referring to all of you to create something great that will be memorable.

I am looking for a basic Business Card Design for my Craft Beer Export company. I sell US Craft Beer in several countries around the globe. Austrailia, China, Taiwan, Chile, France, New Zealand... to name a few.

I am looking for a sleek, modern, and fresh design. Quickly!

Thanks for your consideration!

Cheers,

Dale

Target Market(s)

International

Contact Information for Business Card

Dale Corrigan
Founder- Roaming Hops Guy
Dale@PineLedgeTraders.example
@RoamingHopsGuy- Instagram only
www.Pineledgetraders.example
@PineLedgeTradersAU- Instagram Only

Font styles to use
Serif

Colors
0592cd
ffffff

Requirements
Must have
• Name-
• Title-
• Email-
• Social Media Handle-
• Company Website-
Nice to have
• Nice Logo/ Images on Card
Should not have
• Tacky Beer Images

```html
<!DOCTYPE html>
<html lang="en">
<head>
<meta charset="utf-8">
<title>Pine Ledge Traders — Business Card</title>
<link rel="stylesheet" href="https://fonts.googleapis.com/css2?family=Marcellus&family=Lato:ital,wght@0,400;1,400&display=swap">
<style>
  :root {
    --brand-blue: #0592cd;
    --white: #ffffff;
    --card-paper: #f7f8f9;
    --accent-grey: #9aa3aa;
    --tagline-grey: #6d7378;
    --page-bg: #e6e8ea;
  }
  html, body {
    margin: 0;
    padding: 0;
    width: 1200px;
    height: 900px;
    overflow: hidden;
    background: var(--page-bg);
  }
  .canvas { display: block; width: 1200px; height: 900px; }
  .card-shadow { fill: rgba(0, 0, 0, 0.08); }
  .card-paper { fill: var(--card-paper); }
  .panel-blue { fill: var(--brand-blue); }
  .panel-stripe { fill: var(--accent-grey); }
  .holder-name {
    font-family: "Marcellus", serif;
    font-size: 33px;
    letter-spacing: 1.5px;
    fill: var(--white);
  }
  .holder-title, .contact-line {
    font-family: "Lato", sans-serif;
    fill: var(--white);
  }
  .holder-title { font-size: 23px; }
  .contact-line { font-size: 25px; }
  .contact-icon { fill: var(--white); }
  .contact-icon-cut { fill: var(--brand-blue); }
  .brand-square { fill: var(--brand-blue); }
  .brand-name {
    font-family: "Marcellus", serif;
    font-size: 42px;
    letter-spacing: 2px;
    fill: var(--brand-blue);
  }
  .brand-descriptor {
    font-family: "Lato", sans-serif;
    font-size: 20px;
    letter-spacing: 3px;
    fill: var(--tagline-grey);
  }
  .brand-promise {
    font-family: "Lato", sans-serif;
    font-style: italic;
    font-size: 22px;
    letter-spacing: 1px;
    fill: var(--brand-blue);
  }
</style>
</head>
<body>
<svg class="canvas" viewBox="0 0 1200 900" xmlns="http://www.w3.org/2000/svg" aria-label="Pine Ledge Traders business card">
  <g class="business-card" transform="translate(120 153)">
    <rect class="card-shadow" x="4" y="6" width="960" height="594"/>
    <rect class="card-paper" x="0" y="0" width="960" height="594"/>

    <polygon class="panel-blue" points="0,0 170,0 665,594 0,594"/>
    <polygon class="panel-stripe" points="170,0 212,0 674,594 665,594"/>

    <g class="holder-details">
      <text class="holder-name" x="38" y="313">DALE CORRIGAN</text>
      <text class="holder-title" x="38" y="350">Founder - Roaming Hops Guy</text>

      <g class="contact-email">
        <rect class="contact-icon" x="40" y="383" width="20" height="15"/>
        <polyline points="40,383 50,392 60,383" fill="none" stroke="#0592cd" stroke-width="2"/>
        <text class="contact-line" x="68" y="399">Dale@PineLedgeTraders.example</text>
      </g>
      <g class="contact-web">
        <circle class="contact-icon" cx="50" cy="424" r="9"/>
        <ellipse cx="50" cy="424" rx="4" ry="9" fill="none" stroke="#0592cd" stroke-width="1.5"/>
        <line x1="41" y1="424" x2="59" y2="424" stroke="#0592cd" stroke-width="1.5"/>
        <text class="contact-line" x="68" y="432">www.Pineledgetraders.example</text>
      </g>
      <g class="contact-social">
        <circle class="contact-icon" cx="50" cy="474" r="10"/>
        <text class="contact-line" x="68" y="482">@RoamingHopsGuy</text>
      </g>
      <g class="contact-social">
        <circle class="contact-icon" cx="50" cy="510" r="10"/>
        <text class="contact-line" x="68" y="518">@RoamingHopsGuy</text>
      </g>
    </g>

    <g class="brand-block">
      <rect class="brand-square" x="672" y="78" width="60" height="60"/>
      <text class="brand-name" x="702" y="205" text-anchor="middle">PINE LEDGE</text>
      <text class="brand-name" x="702" y="250" text-anchor="middle">TRADERS</text>
      <text class="brand-descriptor" x="702" y="292" text-anchor="middle">GLOBAL BEVERAGE COMPANY</text>
      <text class="brand-promise" x="702" y="350" text-anchor="middle">100% COLD CHAIN LOGISTICS</text>
    </g>
  </g>
</svg>
</body>
</html>
```